sydney wedding photography business needs a business card design

we need a business card design for a sydney based wedding photography and videography business. our business name is :golden hour studio and film. our target clients are 24-35 yrs female. our style is candid, organic, natural, dynamic. we are a team of young photographers and videographers, and help brides to create memories that they will cherish for the rest of their lives. the logo will be provided. we want an elegant design that reflects our style, and also want to give a great impression to our clients that we are one of the best studios in sydney and our brand means quality and premium service.

Target Market(s)

bride to be, 24-35 years old, living in sydney and surrunding areas

Industry/Entity Type

Wedding Photography

Contact Information for Business Card

address: 57 tarrant street, glenmore nsw 2047
mobile: 0431872259
phone: (02) 9163 2408
info@tidewillowstudio.net.au
www.tidewillowstudio.net.au
facebook:tidewillowweddings
instagram:tidewillowweddings

Font styles to use
Serif
Sans Serif

Requirements
Nice to have
• maybe add my slogan"memories beyond eternity" if the layout looks good
Should not have
• no black color, not good idea for wedding biz card

```html
<!DOCTYPE html>
<html lang="en">
<head>
<meta charset="utf-8">
<title>Golden Hour Studio and Film – Business Card</title>
<link rel="stylesheet" href="https://fonts.googleapis.com/css2?family=Alex+Brush&family=Arimo:wght@400&family=Playfair+Display:wght@700&display=swap">
<style>
  :root {
    --page-bg: #efe9de;
    --mocha-deep: #4a3526;
    --mocha: #5c4331;
    --mocha-light: #6e5140;
    --gold-deep: #a8760a;
    --gold: #d49d16;
    --gold-light: #e8b62a;
    --ink-brown: #3a2818;
    --contact-cream: #f3e6cb;
    --frame-line: rgba(58, 40, 24, 0.55);
    --decor-tint: rgba(232, 182, 42, 0.10);
  }
  * { margin: 0; padding: 0; box-sizing: border-box; }
  html, body {
    width: 1200px;
    height: 950px;
    overflow: hidden;
    background: var(--page-bg);
  }
  .canvas {
    width: 1200px;
    height: 950px;
    display: flex;
    flex-direction: column;
    align-items: center;
    justify-content: center;
    gap: 40px;
  }
  .card {
    width: 680px;
    height: 416px;
    border-radius: 6px;
    box-shadow: 0 14px 30px rgba(74, 53, 38, 0.28);
    overflow: hidden;
    position: relative;
  }

  /* Front */
  .card-front {
    background: linear-gradient(160deg, var(--mocha-light), var(--mocha) 45%, var(--mocha-deep));
    display: grid;
    grid-template-rows: 150px 118px 148px;
  }
  .brand-band {
    display: flex;
    flex-direction: column;
    justify-content: center;
    padding-left: 70px;
  }
  .brand-name {
    font-family: "Playfair Display", serif;
    font-weight: 700;
    color: var(--gold-light);
    line-height: 1;
  }
  .brand-name .brand-main { display: block; font-size: 46px; }
  .brand-name .brand-sub {
    display: block;
    font-size: 15px;
    letter-spacing: 7px;
    text-transform: uppercase;
    margin-top: 10px;
    padding-left: 96px;
  }

  .name-band {
    background: linear-gradient(90deg, var(--gold-deep), var(--gold) 45%, var(--gold-light) 70%, var(--gold));
    position: relative;
    display: flex;
    flex-direction: column;
    align-items: center;
    justify-content: center;
  }
  .corner {
    position: absolute;
    width: 22px;
    height: 22px;
    border: 0 solid var(--frame-line);
  }
  .corner-tl { top: 10px; left: 12px; border-top-width: 1px; border-left-width: 1px; }
  .corner-bl { bottom: 10px; left: 12px; border-bottom-width: 1px; border-left-width: 1px; }
  .corner-tr { top: 10px; right: 12px; border-top-width: 1px; border-right-width: 1px; }
  .corner-br { bottom: 10px; right: 12px; border-bottom-width: 1px; border-right-width: 1px; }

  .person-name {
    font-family: "Alex Brush", cursive;
    font-weight: 400;
    font-size: 56px;
    color: var(--ink-brown);
    line-height: 1;
  }
  .person-role {
    font-family: "Arimo", sans-serif;
    font-size: 15px;
    letter-spacing: 0.5px;
    color: var(--ink-brown);
    margin-top: 4px;
    padding-left: 40px;
  }

  .contact-band {
    position: relative;
    display: flex;
    flex-direction: column;
    justify-content: center;
    align-items: center;
    gap: 6px;
    padding-left: 80px;
  }
  .decor-mark {
    position: absolute;
    right: -50px;
    bottom: -60px;
    width: 170px;
    height: 170px;
  }
  .contact-line {
    position: relative;
    font-family: "Arimo", sans-serif;
    font-size: 15px;
    color: var(--contact-cream);
    letter-spacing: 0.3px;
    text-align: center;
  }

  /* Back */
  .card-back {
    background: linear-gradient(135deg, var(--gold-light), var(--gold) 40%, var(--gold-deep));
  }
</style>
</head>
<body>
  <main class="canvas">
    <section class="card card-front" aria-label="Business card front">
      <div class="brand-band">
        <p class="brand-name">
          <span class="brand-main">golden hour</span>
          <span class="brand-sub">studio and film</span>
        </p>
      </div>

      <div class="name-band">
        <span class="corner corner-tl"></span>
        <span class="corner corner-bl"></span>
        <span class="corner corner-tr"></span>
        <span class="corner corner-br"></span>
        <h1 class="person-name">Clara Bennett</h1>
        <p class="person-role">PHOTOGRAPHER</p>
      </div>

      <div class="contact-band">
        <svg class="decor-mark" viewBox="0 0 170 170" aria-hidden="true">
          <circle cx="85" cy="85" r="80" fill="var(--decor-tint)"/>
        </svg>
        <p class="contact-line">P. (02) 9163 2408 &nbsp;M. 0431 872 259</p>
        <p class="contact-line">E. info@tidewillowstudio.net.au &nbsp;W. tidewillowstudio.net.au</p>
        <p class="contact-line">57 tarrant street, glenmore nsw 2047</p>
      </div>
    </section>

    <section class="card card-back" aria-label="Business card back"></section>
  </main>
</body>
</html>
```